AI Business Tools Landing Page

My web-based website builder (Pavlora.com) will be adding many new features in the very near future and I need an eye-catching landing page to promote these new products.

The page will have a primary section of the 8 main products we are promoting:
1. AI Instant Website Generator
2. AI Chatbot
3. Online Store Builder with AI Assistance
4. AI Auto-Blogging System
5. Online Scheduling System
6. Custom Email System
7. SEO Service
8. CRM System

The page will also have a smaller section for links to our affiliate programs. These can be smaller, less-promanent buttons or links. These are the affiliate products:
1. Get Your LLC
2. Website Design and Maintenance
3. Search Ads Management
4. Social Media Posting Service
5. Logo Design
6. Trademark Registration
7. Patent Application
8. Printing Services (including postcards, flyers, and merch.)
9. Bulk AI Content Generator

The theme and color scheme of the page should follow the theme of our main website, which is https://pavlora.com.

I need the page fully coded and ready to deploy on my server.

I look forward to seeing your amazing designs!

```html
<!DOCTYPE html>
<html lang="en">
<head>
<meta charset="utf-8">
<title>Pavlora – Additional Features &amp; Tools for Website</title>
<link rel="stylesheet" href="https://fonts.googleapis.com/css2?family=Poppins:wght@300;400;500;600;700&display=swap">
<style>
  :root {
    --navy: #0a2447;
    --navy-deep: #061a36;
    --ink: #0d1b2e;
    --accent: #1fa7f0;
    --accent-strong: #0c82e6;
    --line: #8fd3f8;
    --btn-dark: #0c1f4d;
    --muted: #5b6675;
    --footer-text: #c9d5e6;
    --white: #ffffff;
  }
  * { box-sizing: border-box; margin: 0; padding: 0; }
  html, body { width: 864px; height: 1200px; overflow: hidden; background: var(--white); }
  body { font-family: "Poppins", sans-serif; color: var(--ink); position: relative; }

  .hero { position: absolute; left: 0; top: 0; width: 864px; height: 420px; }
  .hero-bg { position: absolute; inset: 0; }
  .brand {
    position: absolute; top: 86px; left: 0; width: 100%;
    display: flex; justify-content: center; align-items: center; gap: 8px;
    color: var(--white); font-weight: 600; font-size: 24px; letter-spacing: -0.3px;
  }
  .brand-mark { width: 14px; height: 14px; background: var(--accent); }
  .hero-title {
    position: absolute; top: 134px; width: 100%; text-align: center; color: var(--white);
  }
  .hero-title strong { display: block; font-weight: 700; font-size: 33px; line-height: 1.15; }
  .hero-title span { display: block; font-weight: 400; font-size: 32px; line-height: 1.25; }
  .hero-rule { position: absolute; top: 219px; left: 408px; width: 54px; height: 2px; background: var(--accent); }

  .feature {
    position: absolute; background: var(--white); border: 1px solid var(--line); border-radius: 4px;
    padding: 16px 8px 0 20px;
  }
  .feature.is-active {
    background: linear-gradient(150deg, #1da2f4 0%, #0c86ea 100%); border-color: #0c86ea; color: var(--white);
  }
  .feature svg { display: block; width: 24px; height: 24px; }
  .feature h3 { font-size: 9.6px; font-weight: 500; line-height: 1.15; margin: 6px 0 7px; white-space: nowrap; }
  .feature ul { list-style: none; }
  .feature li {
    position: relative; font-size: 7.3px; line-height: 1.22; padding-left: 7px; margin-bottom: 9px;
  }
  .feature li::before {
    content: ""; position: absolute; left: 0; top: 3px; width: 2.5px; height: 2.5px; background: var(--accent);
  }
  .feature.is-active li::before { background: #7fd3ff; }

  .divider { position: absolute; top: 681px; left: 50px; width: 765px; height: 1px; background: #a6def8; }
  .divider::after {
    content: ""; position: absolute; left: 380px; top: -2.5px; width: 6px; height: 6px; background: var(--accent);
  }

  .tools-heading {
    position: absolute; top: 735px; width: 100%; text-align: center;
    font-size: 20px; font-weight: 400; color: var(--ink);
  }
  .tools-heading b { font-weight: 700; }

  .tool {
    position: absolute; height: 46px; border: 1.5px solid #46b9f3; border-radius: 3px;
    display: flex; flex-direction: column; justify-content: center; align-items: center;
    color: var(--accent); font-weight: 600; font-size: 11.5px; text-decoration: none;
  }
  .tool.is-active { background: var(--btn-dark); border-color: var(--btn-dark); color: var(--white); }
  .tool small { font-size: 7px; font-weight: 400; color: var(--muted); margin-top: 1px; }

  .footer { position: absolute; left: 0; top: 1000px; width: 864px; height: 200px; }
  .footer-wave { position: absolute; inset: 0; }
  .footer-brand {
    position: absolute; left: 80px; top: 94px; display: flex; align-items: center; gap: 7px;
    color: var(--white); font-weight: 600; font-size: 23px;
  }
  .footer-brand .brand-mark { width: 13px; height: 13px; }
  .copyright {
    position: absolute; left: 0; width: 864px; top: 100px; text-align: center;
    color: var(--footer-text); font-size: 11.5px; font-weight: 300; padding-left: 12px;
  }
  .social { position: absolute; left: 650px; top: 99px; display: grid; grid-template-columns: repeat(5, 15px); gap: 10px 11.5px; }
  .social span { width: 15px; height: 15px; border-radius: 50%; background: var(--white); display: block; }
</style>
</head>
<body>

<header class="hero">
  <svg class="hero-bg" width="864" height="420" viewBox="0 0 864 420" role="img" aria-label="Dark blue technology backdrop of a robot hand reaching toward a human hand">
    <defs>
      <radialGradient id="heroGlow" cx="0.5" cy="0.25" r="0.7">
        <stop offset="0" stop-color="#1c4f86"/>
        <stop offset="0.55" stop-color="#0e2f5c"/>
        <stop offset="1" stop-color="#061a36"/>
      </radialGradient>
    </defs>
    <path d="M0 0 H864 V266 C760 360 600 410 440 407 C260 404 100 372 0 305 Z" fill="url(#heroGlow)"/>
  </svg>
  <div class="brand"><i class="brand-mark"></i>Pavlora</div>
  <h1 class="hero-title"><strong>Additional Features</strong><span>&amp; Tools for Website</span></h1>
  <div class="hero-rule"></div>
</header>

<section class="features">
  <article class="feature" style="left:53px;top:304px;width:185px;height:154px;">
    <svg viewBox="0 0 24 24" fill="none" stroke="#1fa7f0" stroke-width="1"><rect x="1" y="2" width="18" height="17"/><line x1="1" y1="5" x2="19" y2="5"/><line x1="4" y1="9" x2="11" y2="9"/><line x1="4" y1="12" x2="9" y2="12"/><circle cx="17" cy="17" r="5" fill="#fff"/><text x="14.3" y="19" font-size="5" fill="#1fa7f0" stroke="none" font-family="Poppins, sans-serif">AI</text></svg>
    <h3>AI Instant<br>Website Generator</h3>
    <ul>
      <li>Get a professional, SEO-optimized website in seconds!</li>
      <li>Includes custom domain, secure high-speed hosting, professional images, and more!</li>
    </ul>
  </article>

  <article class="feature is-active" style="left:248px;top:304px;width:184px;height:154px;padding-left:18px;">
    <svg viewBox="0 0 24 24" fill="none" stroke="#fff" stroke-width="1"><rect x="8" y="6" width="13" height="8" rx="2"/><circle cx="12.5" cy="10" r="1"/><circle cx="16.5" cy="10" r="1"/><line x1="14.5" y1="3" x2="14.5" y2="6"/><circle cx="14.5" cy="2.5" r="1"/><path d="M2 13 h6 v5 h-3 l-2 2 v-2 h-1 z"/></svg>
    <h3>AI ChatBot</h3>
    <ul>
      <li>Fully-trainable ChatBot will learn about your business to automate the customer support process!</li>
      <li>Built-in CRM features integrate emailing, text messaging, and contact forms!</li>
    </ul>
  </article>

  <article class="feature" style="left:443px;top:304px;width:185px;height:154px;padding-left:14px;padding-right:4px;">
    <svg viewBox="0 0 24 24" fill="none" stroke="#1fa7f0" stroke-width="1"><rect x="1" y="2" width="20" height="17"/><line x1="1" y1="5" x2="21" y2="5"/><path d="M6 9 h2 l1.5 5 h7 l1.5-4 h-9"/><circle cx="10" cy="16" r=".8"/><circle cx="16" cy="16" r=".8"/><path d="M19 17 l3 5 l-1.5 -.5 l-1 1.5 z"/></svg>
    <h3>Online Store Builder<br>(E-Commerce) with AI Assistance</h3>
    <ul>
      <li>Sell you products online and integrate your products into any website!</li>
      <li>Accept payments from multiple payment gateways including Payvia and Cashline!</li>
    </ul>
  </article>

  <article class="feature" style="left:638px;top:304px;width:185px;height:154px;padding-left:16px;">
    <svg viewBox="0 0 24 24" fill="none" stroke="#1fa7f0" stroke-width="1"><rect x="1" y="2" width="18" height="17"/><line x1="1" y1="5" x2="19" y2="5"/><line x1="4" y1="9" x2="11" y2="9"/><line x1="4" y1="12" x2="9" y2="12"/><circle cx="17" cy="17" r="5" fill="#fff"/><text x="14.3" y="19" font-size="5" fill="#1fa7f0" stroke="none" font-family="Poppins, sans-serif">AI</text></svg>
    <h3>AI Auto-Blogging System</h3>
    <ul>
      <li>AI will generate an incredible blog for your business in seconds and immediately begin posting content for you!</li>
      <li>Choose from daily, weekly, or monthly automated blog posting. Consistent, unique, SEO-optimized content posting on cruise control!</li>
    </ul>
  </article>

  <article class="feature" style="left:53px;top:471px;width:185px;height:170px;padding-left:16px;">
    <svg viewBox="0 0 24 24" fill="none" stroke="#1fa7f0" stroke-width="1" style="width:28px;height:28px;"><rect x="1" y="3" width="22" height="15" rx="1"/><rect x="6" y="6" width="12" height="8"/><rect x="7.5" y="7.5" width="2" height="2"/><rect x="11" y="7.5" width="2" height="2"/><rect x="14.5" y="7.5" width="2" height="2"/><rect x="7.5" y="11" width="2" height="2"/><rect x="11" y="11" width="2" height="2"/><rect x="14.5" y="11" width="2" height="2"/><path d="M10 18 v3 h4 v-3 M8 21 h8"/></svg>
    <h3>Online Scheduling<br>System</h3>
    <ul>
      <li>Get appointment bookings, restaurant reservations, or consultations scheduled directly from your website!</li>
      <li>Manage your employees’ schedules and all your appointments from a simple, user-friendly dashboard!</li>
    </ul>
  </article>

  <article class="feature" style="left:247px;top:471px;width:185px;height:170px;padding-left:15px;">
    <svg viewBox="0 0 24 24" fill="none" stroke="#1fa7f0" stroke-width="1" style="width:28px;height:28px;"><rect x="1" y="1" width="22" height="22"/><line x1="1" y1="4" x2="23" y2="4"/><line x1="4" y1="7" x2="20" y2="7"/><rect x="4" y="10" width="16" height="8"/><line x1="4" y1="20" x2="20" y2="20"/><path d="M10 12 l-1.5 2 l1.5 2 M14 12 l1.5 2 l-1.5 2"/></svg>
    <h3>Custom emails using<br>your domain</h3>
    <ul>
      <li>Quickly set up emails for yourself and all your employees with your own domain extension (example – johnd@yoursite.com). No more unprofessional Mailbox and Postly email addresses!</li>
      <li>Manage all your business emails from a simple, user-friendly interface!</li>
    </ul>
  </article>

  <article class="feature" style="left:444px;top:471px;width:185px;height:170px;padding-left:18px;padding-right:4px;">
    <svg viewBox="0 0 24 24" fill="none" stroke="#1fa7f0" stroke-width="1" style="width:28px;height:28px;"><rect x="1" y="1" width="14" height="12"/><line x1="1" y1="4" x2="15" y2="4"/><line x1="3" y1="7" x2="10" y2="7"/><rect x="9" y="10" width="14" height="12" fill="#fff"/><line x1="9" y1="13" x2="23" y2="13"/><path d="M14 19 l4 -4"/><path d="M18 2 a3 3 0 0 1 3 3 M3 16 a3 3 0 0 0 3 3"/></svg>
    <h3>SEO Service – Automatic<br>Backlink Building</h3>
    <ul>
      <li>Let us do the hard work of getting high-quality backlinks to your website. Although difficult to get, backlinks to your website boost search engine ranking more than any other strategy!</li>
      <li>Subscribe now and start getting 10-20 high-quality permanent backlinks to your website every month, guaranteed!</li>
    </ul>
  </article>

  <article class="feature" style="left:638px;top:471px;width:185px;height:170px;padding-left:16px;">
    <svg viewBox="0 0 24 24" fill="none" stroke="#1fa7f0" stroke-width="1" style="width:26px;height:26px;"><circle cx="12" cy="9" r="7.5"/><circle cx="12" cy="8" r="2.5"/><rect x="3" y="14" width="18" height="8" rx="2" fill="#fff"/><text x="5" y="20.2" font-size="5.6" fill="#1fa7f0" stroke="none" font-family="Poppins, sans-serif" font-weight="600">CRM</text></svg>
    <h3>Customer Relationship<br>Management (CRM) System</h3>
    <ul>
      <li>Automate the lead follow up process to consistently stay in front of your potential customers!</li>
      <li>Schedule automatic email and text campaigns and effortlessly follow your funnels from lead to closing!</li>
    </ul>
  </article>
</section>

<div class="divider"></div>

<h2 class="tools-heading">More Tools to Help You <b>Grow Your Business</b></h2>

<nav class="tools">
  <a class="tool" href="https://pavlora.com" style="left:71px;top:799px;width:239px;">Get Your LLC</a>
  <a class="tool is-active" href="https://pavlora.com" style="left:321px;top:799px;width:238px;">Social Media Posting Service</a>
  <a class="tool" href="https://pavlora.com" style="left:567px;top:799px;width:239px;">Patent Application</a>
  <a class="tool" href="https://pavlora.com" style="left:71px;top:856px;width:239px;">Website Design and Maintenance</a>
  <a class="tool" href="https://pavlora.com" style="left:321px;top:856px;width:238px;">Logo Design</a>
  <a class="tool" href="https://pavlora.com" style="left:567px;top:856px;width:239px;">Printing Services<small>(including postcards, flyers, and merch.)</small></a>
  <a class="tool" href="https://pavlora.com" style="left:71px;top:914px;width:239px;">Search Ads Management</a>
  <a class="tool" href="https://pavlora.com" style="left:321px;top:914px;width:238px;">Trademark Registration</a>
  <a class="tool" href="https://pavlora.com" style="left:567px;top:914px;width:239px;">Bulk AI Content Generator</a>
</nav>

<footer class="footer">
  <svg class="footer-wave" width="864" height="200" viewBox="0 0 864 200">
    <path d="M0 17 C260 -2 480 50 640 58 C740 62 820 40 864 27 V200 H0 Z" fill="#2fc0f5"/>
    <path d="M0 22 C260 10 470 62 640 67 C740 70 820 46 864 31 V200 H0 Z" fill="#072346"/>
  </svg>
  <div class="footer-brand"><i class="brand-mark"></i>Pavlora</div>
  <p class="copyright">© 2024 Pavlora. All Rights Reserved</p>
  <div class="social" aria-label="Social media links">
    <span></span><span></span><span></span><span></span><span></span>
    <span></span><span></span><span></span><span></span><span></span>
  </div>
</footer>

</body>
</html>
```